Tidal Forge - Crypto Currency Miner Powered by Renewable Energy Website

We Need Web Pages Design for Website for Crypto Currency Miner

Serivices include:
Mining Rig Sales
Housing for Rigs turnkey on renewable energy grid
Cloud Mining term packages
Updates

http://www.vaultrigsurvey.example (Competitors sites)

Target Market(s)

Investers for Mining Rigs and terms for 1,2 or 3 years of Hash rate

Industry/Entity Type

Mining

Number of Pages Required

5+ page

Font styles to use
Sans Serif

Colors
add136
9bcb3c
606060
474747
ffc214
cadf82
fbee3e
876aae
6b449b

Requirements
Must have
• Pictures of Solar, Wind and power Factor Correction units
Nice to have
• e-commerce platform so contract terms can be purchased through website
Should not have
• Heavy construction equipment

```html
<!DOCTYPE html>
<html lang="en">
<head>
<meta charset="utf-8">
<title>Tidal Forge – Renewable Crypto Mining</title>
<link href="https://fonts.googleapis.com/css2?family=Oswald:wght@300;400;500&family=Roboto+Condensed:wght@400;700&display=swap" rel="stylesheet">
<style>
:root{
  --lime:#add136;
  --green:#9bcb3c;
  --pale-green:#cadf82;
  --gray:#606060;
  --charcoal:#474747;
  --amber:#ffc214;
  --lemon:#fbee3e;
  --violet:#876aae;
  --purple:#6b449b;
  --white:#ffffff;
  --stage:#ececec;
}
*{box-sizing:border-box;margin:0;padding:0}
html,body{width:1200px;height:1200px;overflow:hidden;background:var(--stage)}
body{font-family:"Roboto Condensed",sans-serif;color:var(--charcoal)}
.page{position:absolute;left:446px;top:59px;width:385px;height:1351px;transform:scale(.8);transform-origin:0 0;overflow:hidden;background:var(--white);box-shadow:30px 30px 60px rgba(0,0,0,.22)}
.page > *{position:absolute}
.backdrop{left:0;top:0}
.h{font-family:"Oswald",sans-serif;font-weight:300;line-height:1}
.tiny{font-size:3.2px;line-height:1.35}
.btn{display:block;font-size:4px;text-align:center;line-height:7px;height:8px;border:1px solid var(--lime);color:var(--lime)}
.btn.dark{background:#2b2b2b;border:0;color:var(--white);font-size:6px;line-height:15px;height:15px;border-radius:2px}
.btn.light{border-color:var(--white);color:var(--white)}
.brand{left:63px;top:4px;width:65px;height:67px;background:var(--white);display:flex;flex-direction:column;align-items:center;justify-content:center;gap:4px;box-shadow:0 2px 4px rgba(0,0,0,.15)}
.brand-dot{width:20px;height:20px;border-radius:50%;background:var(--green)}
.brand-name{font-family:"Oswald",sans-serif;font-weight:400;font-size:8.5px;color:var(--charcoal)}
.nav{left:152px;top:20px;display:flex;gap:12px;font-size:3.6px;color:var(--white);letter-spacing:.2px}
.hero-kicker{left:67px;top:82px;width:100px;font-size:4.2px;color:var(--white)}
.hero-title{left:65px;top:104px;font-size:25px;color:var(--white);line-height:1.07}
.hero-copy{left:67px;top:188px;width:115px;color:var(--white)}
.hero-btn{left:67px;top:211px;width:66px}
.login{left:253px;top:152px;width:63px;height:102px;background:var(--amber);border-radius:6px;border:1px solid var(--white);display:flex;flex-direction:column;align-items:center;padding-top:6px;gap:5px}
.login-dot{width:30px;height:30px;border-radius:50%;background:var(--green);border:2px solid var(--white);margin-top:-14px;margin-bottom:8px}
.field{width:46px;height:6px;background:var(--white);border-radius:3px;font-size:3px;line-height:6px;padding-left:9px;color:#aaa}
.remember{font-size:3px;color:var(--white);width:46px}
.login-btn{width:22px;height:6px;border-radius:3px;background:var(--lemon);font-size:3px;line-height:6px;text-align:center;color:#999}
.login-note{font-size:2.6px;color:var(--white)}
.feature{top:268px;width:80px;text-align:center}
.hex{display:block;margin:0 auto 8px}
.feature-title{font-family:"Oswald",sans-serif;font-weight:300;font-size:6.4px;color:var(--gray);line-height:1.25;margin-bottom:6px}
.feature .tiny{color:var(--gray);width:64px;margin:0 auto 7px}
.feature .btn{width:38px;margin:0 auto;border-color:var(--gray);color:var(--gray)}
.divider{width:1px;height:120px;background:#ddd;top:268px}
.section-title{font-family:"Oswald",sans-serif;font-weight:300;font-size:11px;line-height:1.4}
.crypto{left:58px;top:462px;width:116px;color:var(--white)}
.crypto .section-title{border-bottom:1px solid var(--white);padding-bottom:3px;margin-bottom:6px}
.lead{font-size:4.7px;line-height:1.3;margin-bottom:6px}
.crypto .tiny,.why .tiny,.about .tiny{margin-bottom:6px}
.tablet-art{left:193px;top:414px;width:182px;height:204px;background:linear-gradient(135deg,#bcd9f2 0%,#3f7cc8 55%,#7dbb4a 100%)}
.why{left:211px;top:644px;width:116px;color:var(--white)}
.why .section-title,.about .section-title{border-bottom:1px solid var(--lime);padding-bottom:2px;margin-bottom:7px}
.accent{color:var(--lime)}
.tile{width:53px;height:53px;border-radius:3px;display:flex;flex-direction:column;align-items:center;justify-content:flex-end;padding-bottom:6px;gap:6px;font-family:"Oswald",sans-serif;font-weight:300;font-size:5.4px;text-align:center;line-height:1.1}
.tile svg{width:22px;height:22px}
.tile.green{background:var(--green);color:var(--white)}
.tile.amber{background:var(--amber);color:var(--white)}
.tile.lemon{background:var(--lemon);color:var(--charcoal)}
.tile.white{background:var(--white);color:var(--charcoal)}
.about{left:58px;top:860px;width:116px;color:var(--gray)}
.about .section-title{color:var(--charcoal)}
.panel-art{left:173px;top:846px;width:190px;height:160px;background:linear-gradient(135deg,#eef1f6 0%,#5f86cc 45%,#2a4d94 75%,#f2f2f2 100%)}
.pricing{left:62px;top:1050px;width:170px;display:grid;grid-template-columns:42px 42px 42px 43px;font-size:2.8px;text-align:center}
.pricing .cell{height:11.3px;line-height:11.3px;border-bottom:1px solid #fff;border-right:1px solid #fff;background:var(--white);color:var(--gray)}
.pricing .alt{background:#ffe08a}
.pricing .label{text-align:left;padding-left:3px}
.pricing .head{height:36px;line-height:1;display:flex;flex-direction:column;align-items:center;justify-content:flex-start;padding-top:3px;gap:4px;color:var(--white);font-size:4px}
.price{font-family:"Oswald",sans-serif;font-weight:300;font-size:8px}
.prices-copy{left:245px;top:1057px;width:82px;color:var(--charcoal)}
.prices-copy .section-title{border-bottom:1px solid var(--charcoal);padding-bottom:2px;margin-bottom:6px;font-size:10px}
.prices-copy .btn{width:38px;margin-left:42px;border-color:var(--white);color:var(--white)}
.foot-col{top:1249px;color:var(--white)}
.foot-col h4{font-family:"Oswald",sans-serif;font-weight:300;font-size:7px;color:var(--amber);margin-bottom:5px}
.foot-col h4.green{color:var(--lime)}
.foot-col .btn{width:48px;margin-top:8px;border-color:var(--amber);color:var(--amber)}
.socials{display:grid;grid-template-columns:repeat(3,8px);gap:5px;margin-top:12px}
.socials span{width:8px;height:8px;border-radius:50%;border:1px solid var(--white)}
.foot-links{top:1282px;left:208px;display:grid;grid-template-columns:42px 46px 30px;row-gap:6px;font-size:3.6px;color:var(--white)}
</style>
</head>
<body>
<div class="page">
  <svg class="backdrop" width="385" height="1351" viewBox="0 0 385 1351" aria-hidden="true">
    <defs>
      <linearGradient id="heroFill" x1="0" y1="0" x2="1" y2="1">
        <stop offset="0" stop-color="#9bcb3c"/><stop offset=".6" stop-color="#add136"/><stop offset="1" stop-color="#8fbf2e"/>
      </linearGradient>
    </defs>
    <rect width="385" height="1351" fill="#ffffff"/>
    <polygon points="0,0 385,0 385,205 0,267" fill="url(#heroFill)" role="img" aria-label="Wind turbine in a green field"/>
    <polygon points="120,0 385,0 385,22" fill="#ffc214"/>
    <polygon points="0,460 385,398 385,595 0,645" fill="#9bcb3c"/>
    <polygon points="0,645 385,595 385,790 0,850" fill="#474747"/>
    <polygon points="0,1045 385,988 385,1183 0,1245" fill="#ffc214"/>
    <polygon points="0,1245 385,1183 385,1351 0,1351" fill="#474747"/>
  </svg>

  <div class="brand"><span class="brand-dot"></span><span class="brand-name">Tidal Forge</span></div>
  <nav class="nav"><span>HOME</span><span>PRICING</span><span>OUR OFFER</span><span>ABOUT US</span><span>CUSTOMER SERVICE</span></nav>

  <p class="hero-kicker">Join over 1,000,000 people with the world's leading hashpower provider</p>
  <h1 class="h hero-title">START<br>TIDAL FORGE<br>TODAY!</h1>
  <p class="tiny hero-copy">It's super simple – your mining rigs are already set up and running. As soon as you've set up your account you can start to earn your first coins from our renewable-powered data centers.</p>
  <a class="btn dark hero-btn">Learn More</a>

  <form class="login">
    <span class="login-dot"></span>
    <span class="field">Username</span>
    <span class="field">Password</span>
    <span class="remember">● Remember me</span>
    <span class="login-btn">LOG IN</span>
    <span class="login-note">Don't have an account? Register</span>
  </form>

  <div class="feature" style="left:60px">
    <svg class="hex" width="52" height="56" viewBox="0 0 52 56"><polygon points="26,1 51,15 51,41 26,55 1,41 1,15" fill="#ffc214"/><polygon points="26,6 47,18 47,38 26,50 5,38 5,18" fill="none" stroke="#fff" stroke-width="1.5"/><g stroke="#fff" stroke-width="2" fill="none"><line x1="26" y1="28" x2="26" y2="42"/><line x1="26" y1="28" x2="26" y2="17"/><line x1="26" y1="28" x2="35" y2="33"/><line x1="26" y1="28" x2="17" y2="33"/></g></svg>
    <h3 class="feature-title">WIND POWER<br>INVESTMENT</h3>
    <p class="tiny">Don't wrestle with rig assembly and fuel, noisy miners at home. We have the fastest mining hardware running for you already!</p>
    <a class="btn">Learn More</a>
  </div>
  <span class="divider" style="left:145px"></span>
  <div class="feature" style="left:153px">
    <svg class="hex" width="52" height="56" viewBox="0 0 52 56"><polygon points="26,1 51,15 51,41 26,55 1,41 1,15" fill="#add136"/><polygon points="26,6 47,18 47,38 26,50 5,38 5,18" fill="none" stroke="#fff" stroke-width="1.5"/><g stroke="#fff" stroke-width="1.5" fill="none"><rect x="16" y="21" width="20" height="13"/><line x1="16" y1="27.5" x2="36" y2="27.5"/><line x1="22.5" y1="21" x2="22.5" y2="34"/><line x1="29.5" y1="21" x2="29.5" y2="34"/><line x1="26" y1="34" x2="26" y2="40"/></g></svg>
    <h3 class="feature-title">SOLAR POWER<br>INVESTMENT</h3>
    <p class="tiny">Don't wrestle with rig assembly and fuel, noisy miners at home. We have the fastest mining hardware running for you already!</p>
    <a class="btn">Learn More</a>
  </div>
  <span class="divider" style="left:239px"></span>
  <div class="feature" style="left:245px">
    <svg class="hex" width="52" height="56" viewBox="0 0 52 56"><polygon points="26,1 51,15 51,41 26,55 1,41 1,15" fill="#474747"/><polygon points="26,6 47,18 47,38 26,50 5,38 5,18" fill="none" stroke="#fff" stroke-width="1.5"/><g stroke="#fff" stroke-width="1.5" fill="none"><rect x="15" y="22" width="22" height="15" rx="2"/><rect x="29" y="27" width="8" height="5"/><path d="M18 22 L30 16 L33 22"/></g></svg>
    <h3 class="feature-title">GET YOUR FIRST<br>PAYOUT TODAY</h3>
    <p class="tiny">Don't wrestle with rig assembly and fuel, noisy miners at home. We have the fastest mining hardware running for you already!</p>
    <a class="btn">Learn More</a>
  </div>

  <div class="crypto">
    <h2 class="section-title">Buy And Sell<br>Crypto Currency Miner</h2>
    <p class="lead">Lorem ipsum dolor sit amet, consectetur adipisicing elit. Aliquam praesentium, distinctio dicta molestias dignissimos.</p>
    <p class="tiny">Lorem ipsum dolor sit amet consectetur adipisicing elit. Quam earum, possimus vel ad, porro quisquam dolores, blanditiis, nihil pariatur eius adipisci conseq quaerat officiis. Excepturi, sed rerum? Id incidunt nesciunt officiis hic.</p>
    <p class="tiny">Lorem ipsum dolor sit amet consectetur adipisicing elit. Quam earum, possimus vel ad, porro quisquam dolores, blanditiis, nihil pariatur eius adipisci conseq quaerat officiis. Excepturi, sed rerum? Id incidunt nesciunt officiis hic distinctio nihil pariatur lorem ipsum dolor sit amet adipisicing elit quam earum.</p>
    <a class="btn light" style="width:40px;margin-left:75px">Learn More</a>
  </div>
  <div class="tablet-art" role="img" aria-label="Tablet showing a globe with solar panels and wind turbines"></div>

  <div class="tile green" style="left:67px;top:671px"><svg viewBox="0 0 24 24" fill="none" stroke="#fff" stroke-width="1.4"><path d="M12 2 L21 5 V12 C21 17 17 21 12 22 C7 21 3 17 3 12 V5 Z"/><circle cx="12" cy="11" r="3"/><line x1="12" y1="14" x2="12" y2="17"/></svg>Safe And Secure</div>
  <div class="tile amber" style="left:133px;top:671px"><svg viewBox="0 0 24 24" fill="none" stroke="#fff" stroke-width="1.4"><rect x="6" y="2" width="12" height="20" rx="2"/><line x1="10" y1="19" x2="14" y2="19"/><circle cx="12" cy="10" r="3"/></svg>Mobile App</div>
  <div class="tile lemon" style="left:67px;top:733px"><svg viewBox="0 0 24 24" fill="none" stroke="#474747" stroke-width="1.4"><rect x="3" y="7" width="18" height="13" rx="2"/><rect x="14" y="11" width="7" height="5"/><path d="M5 7 L15 3 L17 7"/></svg>Secure Wallet</div>
  <div class="tile white" style="left:133px;top:733px"><svg viewBox="0 0 24 24" fill="none" stroke="#474747" stroke-width="1.4"><rect x="5" y="2" width="13" height="18" rx="1"/><path d="M14 12 L20 14 V18 C20 20 18 22 17 22 C15 22 14 20 14 18 Z"/><line x1="8" y1="7" x2="15" y2="7"/><line x1="8" y1="10" x2="13" y2="10"/></svg>Covered By<br>Insurance</div>

  <div class="why">
    <h2 class="section-title">Why Choose <span class="accent">Tidal Forge</span>?</h2>
    <p class="lead">Lorem ipsum dolor sit amet, consectetur adipisicing elit. Aliquam praesentium, distinctio dicta molestias dignissimos.</p>
    <p class="tiny">Lorem ipsum dolor sit amet consectetur adipisicing elit. Quam earum, possimus vel ad, porro quisquam dolores, blanditiis, nihil pariatur eius adipisci conseq quaerat officiis. Excepturi, sed rerum? Id incidunt nesciunt officiis hic.</p>
    <p class="tiny">Lorem ipsum dolor sit amet consectetur adipisicing elit. Quam earum, possimus vel ad, porro quisquam dolores, blanditiis, nihil pariatur eius adipisci conseq quaerat officiis. Excepturi, sed rerum? Id incidunt nesciunt officiis hic distinctio nihil pariatur lorem ipsum dolor sit amet.</p>
    <a class="btn light" style="width:40px;margin-left:76px">Learn More</a>
  </div>

  <div class="about">
    <h2 class="section-title">About <span class="accent">Tidal Forge</span>?</h2>
    <p class="lead">Lorem ipsum dolor sit amet, consectetur adipisicing elit. Aliquam praesentium, distinctio dicta molestias dignissimos.</p>
    <p class="tiny">Lorem ipsum dolor sit amet consectetur adipisicing elit. Quam earum, possimus vel ad, porro quisquam dolores, blanditiis, nihil pariatur eius adipisci conseq quaerat officiis. Excepturi, sed rerum? Id incidunt nesciunt officiis hic.</p>
    <p class="tiny">Lorem ipsum dolor sit amet consectetur adipisicing elit. Quam earum, possimus vel ad, porro quisquam dolores, blanditiis, nihil pariatur eius adipisci conseq quaerat officiis. Excepturi, sed rerum? Id incidunt nesciunt officiis hic distinctio nihil pariatur lorem ipsum dolor sit amet adipisicing elit quam earum.</p>
    <a class="btn" style="width:40px;margin-left:75px">Learn More</a>
  </div>
  <div class="panel-art" role="img" aria-label="Photo of a solar panel on a mounting pole"></div>

  <div class="pricing">
    <div class="cell head" style="background:var(--lemon);color:var(--charcoal)">TARIF<span style="font-size:2.8px;margin-top:6px">PRICING TABLE</span></div>
    <div class="cell head" style="background:var(--green)">SEMI<span class="price">$29.99</span></div>
    <div class="cell head" style="background:var(--gray)">BASIC<span class="price">$49.99</span></div>
    <div class="cell head" style="background:var(--purple)">PREMIUM<span class="price">$69.99</span></div>

    <div class="cell label">Hashrate per term</div><div class="cell">✕</div><div class="cell">✓</div><div class="cell">✓</div>
    <div class="cell label alt">Monthly allocation</div><div class="cell alt">4 GB</div><div class="cell alt">16 GB</div><div class="cell alt">UNLIMITED</div>
    <div class="cell label">Contracts</div><div class="cell">10 CONTRACTS</div><div class="cell">30 CONTRACTS</div><div class="cell">100 CONTRACTS</div>
    <div class="cell label alt">Daily payout</div><div class="cell alt">✓</div><div class="cell alt">✓</div><div class="cell alt">✓</div>
    <div class="cell label">Green power only</div><div class="cell">✕</div><div class="cell">✕</div><div class="cell">✓</div>
    <div class="cell label alt">Rig monitoring</div><div class="cell alt">✓</div><div class="cell alt">✓</div><div class="cell alt">✓</div>
    <div class="cell label">Account managers</div><div class="cell">1 PERSON</div><div class="cell">4 PERSON</div><div class="cell">170 PERSON</div>
    <div class="cell label alt">Insurance cover</div><div class="cell alt">✕</div><div class="cell alt">✓</div><div class="cell alt">✓</div>
    <div class="cell label">Rig housing</div><div class="cell">✓</div><div class="cell">✓</div><div class="cell">✓</div>
    <div class="cell label alt">Storage</div><div class="cell alt">4 GB</div><div class="cell alt">16 GB</div><div class="cell alt">UNLIMITED</div>
  </div>
  <div class="prices-copy">
    <h2 class="section-title">Prices</h2>
    <p class="lead">Lorem ipsum dolor sit amet, consectetur adipisicing elit. Aliquam praesentium, distinctio dicta molestias.</p>
    <p class="tiny" style="margin-bottom:8px">Lorem ipsum dolor sit amet consectetur adipisicing elit. Quam earum, possimus vel ad, porro quisquam dolores. Nihil pariatur eius adipisci conseq quaerat officiis. Excepturi, sed rerum? Id incidunt nesciunt officiis hic.</p>
    <a class="btn">Learn More</a>
  </div>

  <div class="foot-col" style="left:62px">
    <h4>Member Area</h4>
    <p class="tiny" style="font-size:3.6px">If you don't have an account,<br>sign up for free.</p>
    <a class="btn">SIGN UP</a>
    <a class="btn">LOGIN</a>
  </div>
  <div class="foot-col" style="left:138px">
    <h4 class="green">Follow us</h4>
    <p class="tiny" style="font-size:3.6px">Stay up to date with<br>Tidal Forge activities.</p>
    <div class="socials"><span></span><span></span><span></span><span></span><span></span><span></span></div>
  </div>
  <div class="foot-links">
    <span>HOME</span><span>ABOUT US</span><span>PRIVACY</span>
    <span>PRICING</span><span>DATACENTER</span><span>CONTACT</span>
    <span>OUR OFFER</span><span>PRESS</span><span></span>
  </div>
</div>
</body>
</html>
```